Copperleaf Venture Trust

Take current power point presentation and make it uniform in color and font, and create designs that pop throughout the presentation. Right now, it is dull and mundane.

```html
<!DOCTYPE html>
<html lang="en">
<head>
<meta charset="utf-8">
<title>Copperleaf Venture Trust – Presentation Slides</title>
<link rel="stylesheet" href="https://fonts.googleapis.com/css2?family=Montserrat:wght@400;500;600;700;800;900&display=swap">
<style>
:root{
  --page:#6b6b6b;
  --blue:#1656b8;
  --blue-bright:#2a72e6;
  --navy:#0a1748;
  --navy-deep:#061033;
  --ink:#2b2b2b;
  --body:#444;
  --slate:#4a4a4a;
  --panel:#eef4fc;
  --panel-line:#cfdcef;
  --white:#fff;
}
*{box-sizing:border-box;margin:0;padding:0}
html,body{width:1088px;height:1200px;overflow:hidden}
body{background:var(--page);font-family:"Montserrat",sans-serif;position:relative;color:var(--ink)}
.slide{position:absolute;width:436px;height:246px;background:var(--white);overflow:hidden}
.col-l{left:98px}.col-r{left:554px}
.row-1{top:79px}.row-2{top:345px}.row-3{top:609px}.row-4{top:875px}

.title-pill{position:absolute;left:0;top:14px;height:22px;padding:0 15px 0 21px;background:var(--blue);color:var(--white);
  border-radius:0 11px 11px 0;font-size:12px;font-weight:500;line-height:22px;letter-spacing:.3px;white-space:nowrap}
.brand-mark{position:absolute;right:10px;top:9px;font-size:17px;font-weight:700;color:var(--blue);letter-spacing:.5px;line-height:1}
.footer{position:absolute;left:0;bottom:0;width:100%;height:15px;background:var(--blue);color:var(--white);
  font-size:6.1px;line-height:15px;padding:0 15px;display:flex;justify-content:space-between}

/* cover */
.cover{background:linear-gradient(160deg,#1a4fc4 0%,#1140a8 55%,#0c3592 100%)}
.cover-art{position:absolute;inset:0;background:radial-gradient(ellipse at 70% 70%,rgba(80,150,255,.35),transparent 60%)}
.cover-letters{position:absolute;left:32px;top:46px;font-size:168px;font-weight:800;line-height:1;color:#0d2f7a;letter-spacing:6px}
.cover-name{position:absolute;left:62px;top:183px;font-size:15.5px;font-weight:600;color:var(--white);letter-spacing:2px;white-space:nowrap}

/* team */
.member{position:absolute;top:43px;width:104px}
.member .avatar{width:35px;height:35px;border-radius:50%;background:radial-gradient(circle at 50% 40%,#8a8a8a,#2e2e2e)}
.member h3{font-size:9px;font-weight:500;margin-top:8px;color:var(--ink)}
.member p{font-size:4.6px;line-height:7.3px;color:var(--body);text-align:justify;margin-top:4px;width:102px}

/* agenda */
.agenda-list{position:absolute;left:26px;top:50px;width:210px;list-style:none}
.agenda-list li{font-size:6.6px;line-height:11.3px;display:flex;align-items:center;color:var(--ink)}
.agenda-list li.main::before{content:"";width:8px;height:1px;background:var(--blue);margin-right:5px}
.agenda-list li.sub{padding-left:17px}
.agenda-list li.sub::before{content:"";width:3px;height:3px;border-radius:50%;background:var(--blue);margin-right:3px}
.agenda-list .page{margin-left:auto}
.agenda-photo{position:absolute;left:277px;width:145px;height:48px}
.ph-1{top:43px;background:linear-gradient(135deg,#24405c,#0d1c2c)}
.ph-2{top:99px;background:linear-gradient(135deg,#0f2c3e,#1c4a4f 50%,#0a1a24)}
.ph-3{top:156px;background:linear-gradient(135deg,#0a0e14,#2b3440 60%,#0a0e14)}

/* advantage */
.lead{position:absolute;left:21px;top:48px;font-size:8.8px;font-weight:600;color:var(--ink)}
.pillars{position:absolute;left:14px;top:74px;width:409px;height:133px;display:flex;gap:1px;background:var(--panel-line);border:1px solid var(--panel-line)}
.pillar{flex:1;background:var(--panel);padding:6px 9px}
.pillar h4{background:var(--slate);color:var(--white);font-size:7.6px;font-weight:500;text-align:center;height:16px;line-height:16px}
.pillar ul{list-style:none;margin-top:9px}
.pillar li{font-size:4.4px;line-height:6.5px;color:var(--body);padding-left:5px;position:relative;margin-bottom:6px}
.pillar li::before{content:"";position:absolute;left:0;top:2px;width:2.5px;height:2.5px;border-radius:50%;background:var(--blue)}

/* objectives */
.objectives{background:linear-gradient(120deg,#e9edf2,#f3f5f8 45%,#e3e8ee)}
.objectives-bg{position:absolute;inset:0;background:radial-gradient(ellipse at 75% 60%,rgba(190,160,140,.25),transparent 55%)}
.box-label{position:absolute;height:21px;line-height:21px;text-align:center;font-size:11px;font-weight:500;color:var(--white)}
.goal-label{left:160px;top:24px;width:116px;background:var(--slate)}
.approach-label{left:109px;top:99px;width:218px;background:var(--blue)}
.obj-list{position:absolute;left:62px;list-style:none;width:300px}
.obj-list li{font-size:7.6px;line-height:10.7px;color:var(--body);padding-left:7px;position:relative}
.obj-list li::before{content:"";position:absolute;left:0;top:4px;width:3px;height:3px;border-radius:50%;background:var(--blue)}
.goal-list{top:56px;width:330px}
.approach-list{top:131px}
.flow-arrow{position:absolute;left:213px;top:76px}

/* disclosure */
.disclosure-text{position:absolute;left:21px;top:48px;width:396px}
.disclosure-text p{font-size:5.9px;line-height:8.9px;color:var(--body);text-align:justify;margin-bottom:8.9px}

/* divider */
.divider-photo{position:absolute;left:0;top:0;width:100%;height:156px;background:linear-gradient(180deg,#b9c8d6,#8a98a8 45%,#d8dde2)}
.band-blue{position:absolute;left:0;top:159px;width:100%;height:8px;background:var(--blue)}
.band-slate{position:absolute;left:0;top:170px;width:100%;height:8px;background:var(--slate)}
.divider-title{position:absolute;left:34px;top:203px;font-size:16.5px;font-weight:800;color:var(--blue);letter-spacing:.3px;white-space:nowrap}
.divider-title span{color:var(--navy)}
.divider-brand{position:absolute;left:319px;top:196px;font-size:30px;font-weight:700;color:var(--blue);line-height:1}

/* closing */
.closing{background:var(--navy-deep)}
.closing-globe{position:absolute;left:-40px;top:120px;width:520px;height:260px;border-radius:50% 50% 0 0;
  background:radial-gradient(ellipse at 50% 30%,#1f5fd0 0%,#0f3a9a 35%,#0a1f5c 65%,var(--navy-deep) 100%)}
.closing-brand{position:absolute;left:32px;top:30px;color:var(--blue-bright);font-weight:700}
.closing-brand .mark{font-size:62px;line-height:1;letter-spacing:2px}
.closing-brand .name{font-size:7.6px;letter-spacing:.8px;margin-top:2px}
.thanks{position:absolute;left:236px;top:36px;font-size:27px;font-weight:900;color:var(--white);line-height:1}
.thanks span{color:var(--blue)}
.phone{position:absolute;left:236px;top:75px;display:flex;align-items:center;gap:5px;color:var(--white);font-size:10.5px}
</style>
</head>
<body>

<!-- cover -->
<section class="slide col-l row-1 cover">
  <div class="cover-art" role="img" aria-label="Blue financial chart backdrop"></div>
  <div class="cover-letters">CVT</div>
  <div class="cover-name">Copperleaf Venture Trust</div>
</section>

<!-- senior management -->
<section class="slide col-r row-1">
  <div class="title-pill">SENIOR MANAGEMENT</div>
  <div class="brand-mark">CVT</div>
  <article class="member" style="left:34px">
    <div class="avatar" role="img" aria-label="Portrait of Daniel Ashcroft"></div>
    <h3>Daniel Ashcroft</h3>
    <p>Daniel Ashcroft is a Founder and Member of CVT Investments LLC, bringing over 17 years of experience in PIPE (Private Investment in Public Equity) transactions. Prior to launching his own funds, Mr. Ashcroft co-founded multiple investment funds and managed portfolios for a boutique family of funds. Before joining the family of funds in 2009, he worked as an analyst for an $800 million hedge fund based in Long Island, New York, where he oversaw fifty-five portfolio companies with a focus on private equity financing. Mr. Ashcroft holds a Bachelor of Arts in Finance from Northgate State University.</p>
  </article>
  <article class="member" style="left:167px">
    <div class="avatar" role="img" aria-label="Portrait of Ravi Menon"></div>
    <h3>Ravi Menon</h3>
    <p>Ravi Menon is a Founder and Member of CVT Investments LLC with extensive experience investing in publicly traded companies since 2011. In addition to co-founding multiple investment funds, Mr. Menon’s professional background spans roles at a State Agency, a class action administration firm, and an I.T. company prior to his transition into finance. Mr. Menon earned his Juris Doctor (J.D.) from Harwick University and holds a Bachelor’s degree in Philosophy, Politics, and Law from Northgate State University.</p>
  </article>
  <article class="member" style="left:300px">
    <div class="avatar" role="img" aria-label="Portrait of Thomas Keller"></div>
    <h3>Thomas Keller</h3>
    <p>Thomas Keller is a business executive with extensive C-level and Board of Director leadership experience across multiple privately and publicly held companies. He is currently a Founder and Member of CVT Investments LLC. Previously, Mr. Keller was the Founder, Chairman, and Chief Executive Officer of Meridian Cell Holdings, Inc. (MCHI), a company specializing in harvesting and storing stem cells in the U.S. and internationally, from 2003 to 2012. He also concurrently served as CEO and Chairman of Alder Partners Inc., later absorbed by MCHI in 2005, and as Founder and President of Eastbridge Cell Labs, Inc., a stem cell storage facility in northeastern</p>
  </article>
  <div class="footer"><span>Please refer to the page entitled “General Notes and Risk Factors” when reviewing the information presented herein.</span><span>05</span></div>
</section>

<!-- agenda -->
<section class="slide col-l row-2">
  <div class="title-pill">AGENDA</div>
  <div class="brand-mark">CVT</div>
  <ul class="agenda-list">
    <li class="main">Objectives<span class="page">04</span></li>
    <li class="main">Strategy<span class="page">05</span></li>
    <li class="main">The CVT organization<span class="page">06</span></li>
    <li class="sub">Senior Management</li>
    <li class="sub">CVT’s competitive advantage</li>
    <li class="sub">How we are different</li>
    <li class="main">Performance<span class="page">12</span></li>
    <li class="main">Structure &amp; Terms<span class="page">19</span></li>
    <li class="main">Why Direct Investments?<span class="page">20</span></li>
    <li class="sub">Why CVT’ Direct Invest Strategy?</li>
    <li class="sub">Industry Overview</li>
    <li class="sub">Differentiation Between PIPEs and Direct Investments</li>
    <li class="sub">Capital/Deal Structure</li>
    <li class="sub">Process</li>
    <li class="sub">Protection/Risk</li>
  </ul>
  <div class="agenda-photo ph-1" role="img" aria-label="Dark blue business photo"></div>
  <div class="agenda-photo ph-2" role="img" aria-label="Stock market candlestick chart with hand"></div>
  <div class="agenda-photo ph-3" role="img" aria-label="Hands holding a smartphone"></div>
  <div class="footer"><span>Please refer to the page entitled “General Notes and Risk Factors” when reviewing the information presented herein.</span><span>02</span></div>
</section>

<!-- competitive advantage -->
<section class="slide col-r row-2">
  <div class="title-pill">CVT’S COMPETITIVE ADVANTAGE</div>
  <div class="brand-mark">CVT</div>
  <p class="lead">A Leading direct investment fund in a growing sector with beneficial liquidity terms.</p>
  <div class="pillars">
    <div class="pillar"><h4>PEOPLE</h4><ul>
      <li>Tight and established team and infrastructure. Additional use of outside professionals for reduced overhead and access to top talent.</li>
      <li>Specialized experience with collateralized investments.</li>
      <li>The members have invested or been involved with over $100 million for over 11 years through various market cycles.</li></ul></div>
    <div class="pillar"><h4>PROCESS</h4><ul>
      <li>Proven and rigorous due diligence, portfolio construction and risk management processes.</li></ul></div>
    <div class="pillar"><h4>PHILOSOPHY</h4><ul>
      <li>To pair our rigorous diligence processes, with a disciplined investment approach and strong management to facilitate consistent performance.</li></ul></div>
    <div class="pillar"><h4>PERFORMANCE</h4><ul>
      <li>Consistent annual returns since inception (2015).</li>
      <li>Long-term track record of performance by the Members.</li></ul></div>
  </div>
  <div class="footer"><span>Please refer to the page entitled “General Notes and Risk Factors” when reviewing the information presented herein.</span><span>06</span></div>
</section>

<!-- objectives -->
<section class="slide col-l row-3 objectives">
  <div class="objectives-bg" role="img" aria-label="Faded photo of a business meeting with charts"></div>
  <div class="title-pill">OBJECTIVES</div>
  <div class="brand-mark">CVT</div>
  <div class="box-label goal-label">Investment Goal</div>
  <ul class="obj-list goal-list"><li>Superior risk-adjusted returns while preserving capital in all market environments.</li></ul>
  <svg class="flow-arrow" width="16" height="20" viewBox="0 0 16 20" aria-hidden="true">
    <path d="M6 1 C13 4 13 13 5 16" fill="none" stroke="#777" stroke-width="1.6"/>
    <path d="M2 13 L5 17 L9 14" fill="none" stroke="#777" stroke-width="1.6"/>
  </svg>
  <div class="box-label approach-label">Our Approach to Meeting Objectives</div>
  <ul class="obj-list approach-list">
    <li>Strategically negotiate private investments in publicly traded companies.</li>
    <li>Offer alternative capital solutions for small and micro-cap public companies with market capitalizations up to $2 billion.</li>
    <li>Employ a specialized strategy for collateralized investments.</li>
    <li>Maintain a well-diversified portfolio through tranching and sub-tranching of investments and milestones.</li>
    <li>Execute investments over a 1- to 4-year horizon, ensuring liquidity opportunities throughout.</li>
  </ul>
  <div class="footer"><span>Please refer to the page entitled “General Notes and Risk Factors” when reviewing the information presented herein.</span><span>03</span></div>
</section>

<!-- disclosure -->
<section class="slide col-r row-3">
  <div class="title-pill">DISCLOSURE</div>
  <div class="brand-mark">CVT</div>
  <div class="disclosure-text">
    <p>This Presentation is a summary and does not constitute an offer to sell, or a solicitation of any offer to buy or sell, any securities. Any such offer will be made solely to qualified investors by means of an offering memorandum and related subscription materials, which will contain material information not contained herein. This Presentation is not intended to replace any such offering memorandum.</p>
    <p>No assurance can be given that the objectives discussed herein will be achieved and results may vary substantially on a quarterly, annual or other periodic basis. Past performance is not necessarily indicative of future results.</p>
    <p>Prospective reviewers should not construe this Presentation, any offering memorandum or any other communication received from CVT or its affiliates as legal, accounting, tax, investment or other advice, and each reviewer should consult with its own counsel and advisors as to all legal, tax, regulatory, financial and related matters.</p>
    <p>In addition, certain information contained herein has been provided by third parties and has not been independently verified by CVT. CVT makes no representation or warranty, express or implied, as to the accuracy or the completeness of such information, and accepts no liability for any direct or consequential losses arising from the use of such information.</p>
    <p>This Presentation is confidential and proprietary to CVT. Accordingly, this Presentation is to be treated as strictly confidential and not disclosed, directly or indirectly, to any party other than the person to whom it has been delivered and such person’s professional advisors. Any distribution of this Presentation, in whole or in part, or the divulgence of any of its contents, is unauthorized. No person has been authorized to give any information or make any representations other than as set forth herein.</p>
  </div>
  <div class="footer"><span>Please refer to the page entitled “General Notes and Risk Factors” when reviewing the information presented herein.</span><span>07</span></div>
</section>

<!-- section divider -->
<section class="slide col-l row-4">
  <div class="divider-photo" role="img" aria-label="Team meeting around a table in a bright office with city view"></div>
  <div class="band-blue"></div>
  <div class="band-slate"></div>
  <h2 class="divider-title">SCTION DIVIDER <span>TITLE HERE</span></h2>
  <div class="divider-brand">CVT</div>
</section>

<!-- closing -->
<section class="slide col-r row-4 closing">
  <div class="closing-globe" role="img" aria-label="Glowing blue digital globe with network light trails"></div>
  <div class="closing-brand">
    <div class="mark">CVT</div>
    <div class="name">Copperleaf Venture Trust</div>
  </div>
  <h2 class="thanks"><span>THANK</span> YOU</h2>
  <div class="phone">
    <svg width="13" height="13" viewBox="0 0 20 20" aria-hidden="true">
      <circle cx="10" cy="10" r="10" fill="#fff"/>
      <path d="M6.2 4.8l2 .1 1 2.6-1.3 1c.6 1.4 1.6 2.4 3 3l1-1.3 2.6 1 .1 2c-.1.7-.7 1.2-1.4 1.2C9.1 14.2 5.8 10.9 5 6.2c0-.7.5-1.3 1.2-1.4z" fill="#0a1748"/>
    </svg>
    <span>+1 555 014 2277</span>
  </div>
</section>

</body>
</html>
```